Digital Marketing Agency Landing Page

At VELIM, we offer a comprehensive solution for solar companies' client acquisition needs in the rapidly growing industry. We handle end-to-end client acquisition, meaning we manage the entire lifecycle of capturing new clients—from initial lead generation to delivering the ready-to-buy homeowner. Our expertise in targeted advertising, data analytics, and customer relationship management ensures that we not only find potential customers but also nurture them through tailored engagement strategies until they are ready to make a purchase. By entrusting us with your client acquisition process, solar companies can focus on what they do best—providing sustainable energy solutions—while we work behind the scenes to grow your customer base and increase your market share.

We need to restructure our website to make it more professional. We don't need any complex functionalities. We are looking for someone that is good in design and can build a visually aesthetic website following our brand image. We only need a landing page and a lead form in the end. I would like to have only one page, but a relatively big one where people scroll down. I would like to have a minimal and classy look. Something that is timeless and elegant.

Structure:

initial page
About us
How we operate
Get in touch

Target Market(s)

Solar Comapanies

Industry/Entity Type

Marketing solautions

Coding

Coded - Design and coding required

Number of Pages Required

1 page

Requirements
Nice to have
• Inspirations: https://www.qz.zu/ https://www.marchbeck.example/ https://www.tovanrid.example/ https://pruvo.example/

```html
<!DOCTYPE html>
<html lang="en">
<head>
<meta charset="utf-8">
<title>VELIM — Client Acquisition for Solar Companies</title>
<link href="https://fonts.googleapis.com/css2?family=Montserrat:wght@300;400;500;600;700&display=swap" rel="stylesheet">
<style>
:root{
  --navy:#14202e;
  --navy-soft:#1d2b3b;
  --ink:#1b1b1b;
  --muted:#8a8a8a;
  --label:#555;
  --white:#ffffff;
  --paper:#f4f4f4;
  --field:#fbf9f4;
  --field-line:#e6e1d6;
  --line:#d8d8d8;
  --sand:#f4efe3;
  --hero-a:#8f7a63;
  --hero-b:#3e5a82;
  --hero-c:#c9b9a2;
}
*{box-sizing:border-box;margin:0;padding:0}
html,body{width:1200px;height:2487px;overflow:hidden}
body{position:relative;background:var(--white);font-family:"Montserrat",sans-serif;color:var(--ink)}
.abs{position:absolute}

/* header */
.site-header{left:0;top:0;width:1200px;height:113px;background:var(--navy)}
.brand{left:111px;top:24px;width:171px;height:66px;border:1px solid rgba(255,255,255,.75);display:flex;align-items:center;justify-content:center;color:var(--white);font-weight:300;font-size:38px;letter-spacing:1px}
.brand::after{content:"";position:absolute;left:6px;top:6px;right:-6px;bottom:-6px;border:1px solid rgba(255,255,255,.55)}
.nav-link{top:46px;color:var(--white);font-size:16px;font-weight:400;text-decoration:none}
.nav-cta{left:946px;top:36px;width:141px;height:43px;border:1px solid var(--white);color:var(--white);display:flex;align-items:center;justify-content:center;font-size:17px}
.nav-cta::after{content:"";position:absolute;inset:3px;border:1px solid rgba(255,255,255,.8)}

/* hero */
.hero{left:0;top:113px;width:1200px;height:514px;background:linear-gradient(100deg,var(--hero-b) 0%,#6b7f9c 30%,var(--hero-a) 60%,#5a4535 100%)}
.hero-orb{border-radius:50%}
.orb-one{left:947px;top:131px;width:204px;height:204px;background:radial-gradient(circle at 40% 35%,#e9eef6,#8fa4c9 60%,#3f5f98)}
.orb-two{left:1049px;top:339px;width:200px;height:200px;background:radial-gradient(circle at 60% 40%,#f0b03c,#d2433a 45%,#dfe3ea 70%)}
.welcome{left:103px;top:230px;width:387px;height:333px;border:1px solid rgba(255,255,255,.8)}
.welcome::after{content:"";position:absolute;left:8px;top:8px;right:-8px;bottom:-8px;border:1px solid rgba(255,255,255,.7)}
.welcome-kicker{left:116px;top:244px;color:var(--white);font-size:27px;font-weight:400}
.welcome-title{left:114px;top:290px;color:var(--white);font-size:60px;font-weight:400;letter-spacing:1px}
.welcome-text{left:116px;top:386px;width:360px;color:var(--white);font-size:17.5px;line-height:27px}
.btn-light{left:116px;top:482px;width:167px;height:44px;border:1px solid var(--white);color:var(--white);display:flex;align-items:center;justify-content:center;font-size:17px}
.btn-light::after{content:"";position:absolute;inset:3px;border:1px solid rgba(255,255,255,.8)}
.edge-line{height:1px;background:#5b6878}

/* paper band */
.paper{left:0;top:627px;width:1200px;height:956px;background:linear-gradient(180deg,var(--paper),#f7f7f7 80%,#efefef)}

/* contact */
.contact-card{left:111px;top:569px;width:978px;height:470px;background:var(--white);box-shadow:0 4px 14px rgba(0,0,0,.1)}
.contact-frame{border:1px solid #ececec}
.section-title{width:1200px;left:0;text-align:center;font-weight:400;color:var(--ink)}
.field-label{font-size:17px;color:var(--label)}
.field{background:var(--field);border:1px solid var(--field-line)}
.btn-dark{border:1px solid var(--ink);display:flex;align-items:center;justify-content:center;font-size:17px;color:var(--ink);background:var(--white)}
.btn-dark::after{content:"";position:absolute;inset:3px;border:1px solid var(--ink)}

/* services */
.service-card{border:1px solid #e4e4e4;background:rgba(255,255,255,.4)}
.service-card::after{content:"";position:absolute;left:8px;top:8px;right:-8px;bottom:-8px;border:1px solid #e9e9e9}
.service-photo{left:5px;top:5px;right:5px;bottom:12px}
.service-name{font-size:23px;text-align:center;font-weight:400;line-height:26px}
.carousel-arrow{top:1316px;width:36px;height:32px}

/* about */
.about-text{left:119px;width:460px;font-size:16.2px;line-height:24px;color:var(--muted)}
.collage-frame{border:1px solid var(--ink)}
.mark-tile{left:601px;top:1747px;width:141px;height:129px;background:var(--navy);display:flex;align-items:center;justify-content:center}
.mark-square{width:100px;height:100px;border:1px solid var(--white);display:flex;align-items:center;justify-content:center;color:var(--white);font-size:24px;font-weight:300;letter-spacing:1px}

/* footer */
.site-footer{left:0;top:2142px;width:1200px;height:345px;background:var(--navy)}
.footer-brand{left:522px;top:2191px;width:155px;height:58px;border:1px solid rgba(255,255,255,.75);display:flex;align-items:center;justify-content:center;color:var(--white);font-size:32px;font-weight:300;letter-spacing:1px}
.footer-brand::after{content:"";position:absolute;inset:5px;border:1px solid rgba(255,255,255,.55)}
.social{top:2208px;width:20px;height:20px;border-radius:50%;background:var(--white)}
.footer-text{color:var(--white);font-size:15.5px;line-height:24px}
.footer-head{font-weight:600;font-size:17px}
.footer-list{list-style:none}
.footer-list li::before{content:"» "}
.copyright{left:0;top:2459px;width:1200px;text-align:center;color:var(--white);font-size:16px}
</style>
</head>
<body>

<header class="abs site-header">
  <div class="abs brand">VELIM</div>
  <a class="abs nav-link" style="left:546px">Home</a>
  <a class="abs nav-link" style="left:662px">About Us</a>
  <a class="abs nav-link" style="left:803px">Services</a>
  <a class="abs nav-cta">Contact Us</a>
</header>

<section class="abs hero" role="img" aria-label="Photo of a presenter pointing at charts on a large screen in a meeting room"></section>
<div class="abs hero-orb orb-one" role="img" aria-label="Round photo of a hand holding a glowing energy globe over solar panels"></div>
<div class="abs hero-orb orb-two" role="img" aria-label="Round illustration of solar panels beside an energy-rating scale"></div>
<div class="abs welcome"></div>
<div class="abs welcome-kicker">Welcome To</div>
<h1 class="abs welcome-title">VELIM</h1>
<p class="abs welcome-text">Lorem ipsum dolor sit amet, consectetur adipiscing elit..</p>
<a class="abs btn-light">Get Started</a>

<div class="abs edge-line" style="left:8px;top:628px;width:110px"></div>
<div class="abs edge-line" style="left:16px;top:638px;width:102px"></div>
<div class="abs edge-line" style="left:1089px;top:628px;width:111px"></div>
<div class="abs edge-line" style="left:1089px;top:638px;width:111px"></div>

<div class="abs paper"></div>

<section class="abs contact-card">
  <div class="abs contact-frame" style="left:21px;top:20px;width:926px;height:418px"></div>
  <div class="abs contact-frame" style="left:31px;top:30px;width:926px;height:418px"></div>
</section>
<h2 class="abs section-title" style="top:624px;font-size:27px">Contact Us</h2>
<label class="abs field-label" style="left:173px;top:696px">Full Name</label>
<div class="abs field" style="left:294px;top:690px;width:243px;height:30px"></div>
<label class="abs field-label" style="left:661px;top:696px">Last Name</label>
<div class="abs field" style="left:783px;top:690px;width:242px;height:30px"></div>
<label class="abs field-label" style="left:173px;top:765px">E - Mail</label>
<div class="abs field" style="left:294px;top:759px;width:243px;height:30px"></div>
<label class="abs field-label" style="left:661px;top:765px">Phone</label>
<div class="abs field" style="left:783px;top:759px;width:242px;height:30px"></div>
<label class="abs field-label" style="left:173px;top:833px">Message</label>
<div class="abs field" style="left:294px;top:827px;width:731px;height:67px"></div>
<a class="abs btn-dark" style="left:294px;top:931px;width:167px;height:44px">SUBMIT</a>

<h2 class="abs section-title" style="top:1113px;font-size:35px">Our Services</h2>

<svg class="abs carousel-arrow" style="left:45px" viewBox="0 0 36 32" aria-hidden="true">
  <g fill="none" stroke="#9a9a9a" stroke-width="1.5"><path d="M20 2 6 16l14 14"/><path d="M26 2 12 16l14 14"/><path d="M32 2 18 16l14 14"/></g>
</svg>
<svg class="abs carousel-arrow" style="left:1120px" viewBox="0 0 36 32" aria-hidden="true">
  <g fill="none" stroke="#9a9a9a" stroke-width="1.5"><path d="M16 2l14 14-14 14"/><path d="M10 2l14 14-14 14"/><path d="M4 2l14 14-14 14"/></g>
</svg>

<div class="abs service-card" style="left:114px;top:1194px;width:303px;height:273px">
  <div class="abs service-photo" style="background:linear-gradient(135deg,#f7f3ea,#f1e6d2 50%,#e9eef3)" role="img" aria-label="Marketing illustration with colourful speech bubbles"></div>
</div>
<div class="abs service-card" style="left:444px;top:1194px;width:312px;height:273px">
  <div class="abs service-photo" style="background:linear-gradient(160deg,#b9c6cf,#6f7f8c 55%,#2f3d4c)" role="img" aria-label="Photo of a team meeting in a glass-walled office"></div>
</div>
<div class="abs service-card" style="left:775px;top:1194px;width:312px;height:273px">
  <div class="abs service-photo" style="background:linear-gradient(120deg,#9aa3ad,#5a5352 50%,#c7ccd2)" role="img" aria-label="Photo of a customer support agent with a headset at a laptop"></div>
</div>
<div class="abs service-name" style="left:114px;top:1484px;width:303px">Advertising</div>
<div class="abs service-name" style="left:444px;top:1484px;width:302px">Data Analytics</div>
<div class="abs service-name" style="left:775px;top:1484px;width:312px">Customer Relationship Management</div>

<h2 class="abs section-title" style="top:1611px;font-size:35px">About Us</h2>
<p class="abs about-text" style="top:1685px">Lorem ipsum dolor sit amet, consectetur adipiscing elit, sed do eiusmod tempor incididunt ut labore et dolore magna aliqua. Ut enim ad minim veniam, quis nostrud exercitation ullamco laboris nisi ut aliquip ex ea commodo consequat. Duis aute irure dolor in reprehenderit in voluptate velit esse cillum dolore eu fugiat nulla pariatur.</p>
<p class="abs about-text" style="top:1867px">Lorem ipsum dolor sit amet, consectetur adipiscing elit, sed do eiusmod tempor incididunt ut labore et dolore magna aliqua. Ut enim ad minim veniam, quis nostrud exercitation ullamco laboris.</p>
<a class="abs btn-dark" style="left:120px;top:2012px;width:168px;height:44px">Read More</a>

<div class="abs collage-frame" style="left:682px;top:1708px;width:406px;height:248px"></div>
<div class="abs collage-frame" style="left:690px;top:1716px;width:390px;height:240px;border-top:none;border-left:none"></div>
<div class="abs" style="left:672px;top:1701px;width:399px;height:241px;background:linear-gradient(135deg,#8a6a4e,#c9a986 45%,#e8e2d8 75%,#6d7a86)" role="img" aria-label="Overhead photo of a team working around a wooden table with laptops and documents"></div>
<div class="abs mark-tile"><div class="mark-square">VELIM</div></div>
<div class="abs" style="left:601px;top:1876px;width:308px;height:180px;background:linear-gradient(180deg,#c9dcea 0%,#9fbdd6 40%,#3b4f6e 75%,#2a3854)" role="img" aria-label="Photo of workers installing solar panels on a roof"></div>

<div class="abs" style="left:18px;top:2123px;width:1182px;height:19px;background:var(--sand)"></div>
<div class="abs edge-line" style="left:8px;top:2123px;width:1192px;background:#333"></div>
<div class="abs edge-line" style="left:18px;top:2131px;width:1182px;background:#333"></div>

<footer class="abs site-footer"></footer>
<div class="abs footer-brand">VELIM</div>
<span class="abs social" style="left:933px" aria-label="Social link"></span>
<span class="abs social" style="left:973px" aria-label="Social link"></span>
<span class="abs social" style="left:1019px" aria-label="Social link"></span>
<span class="abs social" style="left:1066px" aria-label="Social link"></span>

<p class="abs footer-text" style="left:115px;top:2297px;width:270px">Lorem ipsum dolor sit amet, consectetur adipiscing elit, sed do eiusmod tempor incididunt ut labore et dolore magna aliqua. Ut enim ad</p>

<div class="abs footer-text" style="left:462px;top:2303px">
  <div class="footer-head">Information</div>
  <ul class="footer-list"><li>Home</li><li>About Us</li><li>Service</li><li>Contact <b>Us</b></li></ul>
</div>
<div class="abs footer-text" style="left:685px;top:2303px">
  <div class="footer-head">Information</div>
  <ul class="footer-list"><li>Blog</li><li>FAQ</li><li>Our Clients</li><li>Join Us</li></ul>
</div>
<div class="abs footer-text" style="left:917px;top:2303px">
  <div class="footer-head">Have Any Question?</div>
  <div style="display:flex;align-items:center;gap:8px">
    <svg width="15" height="15" viewBox="0 0 16 16" aria-hidden="true"><path d="M15 1 1 7l6 2 2 6z" fill="#fff"/></svg>Lorem ipsum dolor</div>
  <div style="display:flex;align-items:center;gap:10px">
    <svg width="15" height="12" viewBox="0 0 16 12" aria-hidden="true"><rect x="1" y="1" width="14" height="10" fill="none" stroke="#fff" stroke-width="1.5"/><path d="M1 1l7 6 7-6" fill="none" stroke="#fff" stroke-width="1.5"/></svg>info @ velim.example</div>
  <div style="display:flex;align-items:center;gap:10px">
    <svg width="13" height="13" viewBox="0 0 16 16" aria-hidden="true"><path d="M3 1l3 0 1 4-2 1.5a9 9 0 0 0 4.5 4.5L11 9l4 1v3c0 1-1 2-2 2C7 15 1 9 1 3c0-1 1-2 2-2z" fill="#fff"/></svg>+(555) 010 2040</div>
</div>

<p class="abs copyright">Copyright @ 2023 - VELIM - All Rights Reserved</p>

</body>
</html>
```